Website redesign for Law Firm

Looking for someone experienced in Wordpress to redesign our existing website as part of a rebrand. The scope of the redesign includes:

1. Change logo and colours throughout to match new name and branding (minimal pink, mainly light and dark blue)
2. Redesign to focus of converison rate optimisation and modernisation. The focus is conveyancing and the call to action is Request an Instant Quote
3. Remove Meet the Leadership Team section from homepage
4. Remove Meet the Team section from About Us Page
5. Change ribbon to have Special Conditions and Blog as their own tabs, not a drop down under Resources
6. Include a Get a Free Quote section on the homepage similar to settlewise.com.au, however does not require a State section. This calculator is to be coded into the final design and there will only be 3 different prices depending on what they choose

SLUG/Page stucture must stay the same for the final coded design.

Wanting something that is very clean and conversion rate optimised.

The existing website is okaforlegal.com.au. It is moving to tallowcreeklawyers.com.au and changing name to Tallow Creek Lawyers.

The logo design files can be found here: https://files.quillbox.net/share/7kR2mXv9PqL4nWc8TzY3hJ5dBfG6sA1e?view=shared

The colour codes and font name are included there also. You must use the correct colour codes from the logo. You can add a lighter blue to be the contract colour also. The pink colour is not to be a main colour it is just a feature colour to be used minimally. The dark blue from the background of the inverse (hex 192330) and a lighter blue are the main colours. Lots of white space and not all a dark background.

Examples of other websites in the industy

- https://keyturnsettlements.com/
- https://www.settlewise.com.au/
- https://truelinetransfers.com.au/

Target Market(s)

Professionals buying and selling property

Industry/Entity Type

Legal

Coding

Coded - Design and coding required

Number of Pages Required

5+ page

Colors
0054AA
0677BA
7BADD7
CADEEF
E8F1F8

Requirements
Must have
• Wordpress and Elementor, Blue colour scheme.
Nice to have
• Get creative with the redesign/layout and focus on converison rate, especially above the fold. The existing layout does not need to stay the same
Should not have
• Minimal of the pink

```html
<!DOCTYPE html>
<html lang="en">
<head>
<meta charset="utf-8">
<title>Tallow Creek Lawyers — Property Law</title>
<link href="https://fonts.googleapis.com/css2?family=Barlow:wght@500;600&family=Jost:wght@400;500&display=swap" rel="stylesheet">
<style>
:root{
  --navy:#192330;
  --blue:#0054AA;
  --blue-mid:#0677BA;
  --blue-soft:#7BADD7;
  --blue-pale:#CADEEF;
  --blue-wash:#E8F1F8;
  --pink:#ec1a5c;
  --white:#ffffff;
  --text:#2b3440;
  --muted:#505a66;
}
*{box-sizing:border-box;margin:0;padding:0}
html,body{width:1200px;height:5102px;overflow:hidden}
body{position:relative;background:var(--white);font-family:'Jost',sans-serif;color:var(--text)}
.abs{position:absolute}
h1,h2,h3,h4{font-family:'Barlow',sans-serif;font-weight:500;text-transform:uppercase}
.accent{display:inline-block;width:6px;height:6px;background:var(--pink);margin-left:5px;vertical-align:baseline}
.btn{position:absolute;background:var(--blue-mid);color:#fff;font-family:'Barlow',sans-serif;font-weight:600;font-size:13px;letter-spacing:.5px;text-transform:uppercase;display:flex;align-items:center;justify-content:center;border-radius:3px}
.section-title{position:absolute;left:0;width:1200px;text-align:center;font-size:27px;letter-spacing:.5px;color:var(--navy)}

/* header */
.topbar{top:0;left:0;width:1200px;height:115px;background:var(--navy)}
.logo{left:110px;top:16px;color:#fff;font-family:'Jost',sans-serif;font-size:17px;letter-spacing:9px;line-height:28px}
.contact-item{display:flex;align-items:center;gap:20px;color:#fff;font-size:14px;line-height:28px}
.icon-ring{width:42px;height:42px;border:1px solid rgba(255,255,255,.5);border-radius:50%;display:flex;align-items:center;justify-content:center;flex:none}
.nav{top:115px;left:0;width:1200px;height:43px;background:var(--blue)}
.nav a{position:absolute;top:14px;color:#fff;font-family:'Barlow',sans-serif;font-weight:500;font-size:13px;text-decoration:none}
.nav .cta{top:0;left:916px;width:172px;height:43px;background:#fff;color:var(--navy);display:flex;align-items:center;justify-content:center;font-size:15px;letter-spacing:.5px}

/* hero */
.hero{top:158px;left:0;width:1200px;height:442px;background:linear-gradient(100deg,#4e5159 0%,#6c6e72 45%,#8c8a86 70%,#a29a8e 100%)}
.hero-shade{top:0;left:0;width:1200px;height:442px;background:linear-gradient(90deg,rgba(25,35,48,.6),rgba(25,35,48,0) 60%)}
.hero h1{left:110px;top:95px;color:#fff;font-size:31px;line-height:45px;letter-spacing:.3px}
.hero h1 span{color:var(--blue-soft)}
.hero p{left:110px;top:196px;width:470px;color:#fff;font-size:14px;line-height:35px}

/* help */
.help-text{top:728px;left:195px;width:810px;text-align:center;font-size:14px;line-height:34px;color:var(--muted)}
.card{position:absolute;top:884px;width:316px;height:334px;background:#fff;box-shadow:0 2px 12px rgba(0,0,0,.08);text-align:center;padding:0 22px}
.card.dark{background:var(--navy)}
.card .badge{width:62px;height:62px;border-radius:50%;background:var(--blue);margin:28px auto 0;display:flex;align-items:center;justify-content:center}
.card.dark .badge{background:#fff}
.card h3{margin-top:22px;font-size:21px;line-height:40px;color:var(--navy)}
.card.dark h3{color:var(--blue-soft)}
.card p{margin-top:14px;font-size:13.5px;line-height:34px;color:var(--muted)}
.card.dark p{color:#fff}
.chev{position:absolute;width:20px;height:20px}

/* services */
.services{top:1300px;left:0;width:1200px;height:1085px;background:var(--blue-wash)}
.timeline{left:599px;top:1412px;height:850px;border-left:2px dashed var(--blue-soft)}
.tl-dot{left:596px;top:1407px;width:8px;height:8px;border-radius:50%;background:var(--pink)}
.tl-icon{width:70px;height:70px;border-radius:50%;background:#fff;border:1px solid var(--blue-mid);display:flex;align-items:center;justify-content:center}
.svc h3{font-size:20px;color:var(--blue);letter-spacing:.3px}
.svc p{font-size:13.5px;line-height:34px;color:var(--muted);margin-top:18px}
.photo{position:absolute}

/* quote */
.quote-band{top:2385px;left:0;width:1200px;height:383px;background:var(--navy)}
.quote-card{top:2524px;left:143px;width:915px;height:541px;background:#fff;box-shadow:0 4px 18px rgba(0,0,0,.1)}
.pill{position:absolute;height:30px;border:1px solid #777;border-radius:4px;font-size:13px;display:flex;align-items:center;justify-content:center;color:var(--text);padding:0 10px}
.field{position:absolute;top:186px;width:199px;height:42px;border:1px solid #c8c8c8;border-radius:3px;font-size:12px;color:#999;padding:12px 10px}
.q-label{position:absolute;font-size:14px;color:var(--blue);line-height:30px}

/* testimonials */
.review{position:absolute;top:3150px;width:282px;height:290px;background:var(--blue-wash);padding:18px 20px}
.stars{display:flex;gap:5px}
.stars span{width:15px;height:15px;background:#f6b21b;clip-path:polygon(50% 0,61% 35%,98% 35%,68% 57%,79% 91%,50% 70%,21% 91%,32% 57%,2% 35%,39% 35%)}
.review p{margin-top:22px;font-size:13.5px;font-style:italic;line-height:32px;color:var(--text)}
.reviewer{position:absolute;left:20px;top:248px;display:flex;align-items:center;gap:20px}
.avatar{width:58px;height:58px;border-radius:50%;flex:none}
.reviewer b{display:block;font-family:'Barlow',sans-serif;font-weight:600;font-size:13px;color:var(--blue);text-transform:uppercase}
.reviewer small{font-size:12px;color:var(--text)}
.rmark{position:absolute;right:14px;top:16px;width:14px;height:14px;border-radius:50%;background:var(--blue-soft)}
.round-arrow{position:absolute;width:32px;height:32px;border:1.5px solid var(--navy);border-radius:50%;display:flex;align-items:center;justify-content:center}

/* get started */
.started{top:3540px;left:0;width:1200px;height:310px;background:var(--navy)}

/* blog */
.post{position:absolute;top:4022px;width:313px;height:478px;background:#fff;box-shadow:0 2px 12px rgba(0,0,0,.1)}
.post .img{margin:0 8px;height:220px;border-radius:10px}
.post h4{margin:36px 22px 0;font-size:16px;line-height:33px;color:var(--navy);font-weight:600}
.post p{margin:16px 22px 0;font-size:13px;line-height:32px;color:var(--muted)}

/* offer */
.offer{top:4585px;left:0;width:1200px;height:112px;background:var(--blue)}

/* footer */
.footer{top:4697px;left:0;width:1200px;height:405px;background:var(--navy);color:#fff}
.footer h4{font-size:22px;color:var(--blue-soft)}
.footer li{list-style:none;font-size:14.5px;line-height:38px}
.footer .icon-ring{border-color:var(--blue-soft)}
</style>
</head>
<body>

<!-- header -->
<div class="abs topbar">
  <div class="abs logo">TALLOW<br>CREEK<br>LAWYERS</div>
  <div class="abs contact-item" style="left:458px;top:28px">
    <div class="icon-ring"><svg width="18" height="18" viewBox="0 0 24 24"><path fill="#7BADD7" d="M6.6 10.8c1.4 2.8 3.8 5.1 6.6 6.6l2.2-2.2c.3-.3.7-.4 1-.2 1.1.4 2.3.6 3.6.6.6 0 1 .4 1 1V20c0 .6-.4 1-1 1C10.6 21 3 13.4 3 4c0-.6.4-1 1-1h3.5c.6 0 1 .4 1 1 0 1.3.2 2.5.6 3.6.1.3 0 .7-.2 1l-2.3 2.2z"/></svg></div>
    <div>Call Us<br>(07) 3184 2290</div>
  </div>
  <div class="abs contact-item" style="left:732px;top:28px">
    <div class="icon-ring"><svg width="18" height="18" viewBox="0 0 24 24"><rect x="2" y="5" width="20" height="14" rx="2" fill="#7BADD7"/><path d="M3 6l9 7 9-7" stroke="#192330" stroke-width="1.6" fill="none"/></svg></div>
    <div>Email Us<br>mail@tallowcreeklawyers.com.au</div>
  </div>
</div>
<nav class="abs nav">
  <a style="left:110px;border-bottom:1px solid #fff">HOME</a>
  <a style="left:212px">SERVICES</a>
  <a style="left:335px">RESOURCES</a>
  <a style="left:476px">ABOUT US</a>
  <a style="left:604px">BLOG</a>
  <a style="left:702px">CONTACT US</a>
  <a class="cta">GET A FREE QUOTE</a>
</nav>

<!-- hero -->
<section class="abs hero">
  <div class="abs" role="img" aria-label="Three property professionals in business attire standing in a bright, empty apartment" style="left:600px;top:0;width:600px;height:442px;background:linear-gradient(180deg,#7d7c79,#9b948a 70%,#b6a58e)"></div>
  <div class="abs hero-shade"></div>
  <h1 class="abs">We help property developers,<br><span>Buyers &amp; Sellers</span> like you</h1>
  <p class="abs">All we do is property law. Rely on our experience to help make your next property transaction a success.</p>
  <div class="btn" style="left:110px;top:292px;width:186px;height:37px">Request an instant quote</div>
</section>

<!-- how can we help -->
<h2 class="section-title" style="top:677px">How can we help you?<span class="accent"></span></h2>
<p class="abs help-text">Tallow Creek Lawyers are specialised property development law firm based in Kedron, Brisbane. We provide legal services to property developers for land, unit, house, and townhouse developments of all sizes, as well as conveyancing law services for buyers and sellers.</p>
<svg class="chev" style="left:38px;top:1041px" viewBox="0 0 20 20"><path d="M13 3L6 10l7 7" stroke="#192330" stroke-width="2" fill="none"/></svg>
<svg class="chev" style="left:1132px;top:1041px" viewBox="0 0 20 20"><path d="M7 3l7 7-7 7" stroke="#192330" stroke-width="2" fill="none"/></svg>
<div class="card" style="left:110px">
  <div class="badge"><svg width="30" height="30" viewBox="0 0 30 30"><path d="M5 26V10h8v16M15 26V4h10v22M3 26h24" stroke="#fff" stroke-width="2" fill="none"/></svg></div>
  <h3>Development site<br>acquisitions &amp; sales</h3>
  <p>Thorough due diligence and a contract that protects your rights and interests, every time.</p>
</div>
<div class="card dark" style="left:443px">
  <div class="badge"><svg width="28" height="28" viewBox="0 0 28 28"><rect x="6" y="3" width="16" height="22" rx="2" stroke="#192330" stroke-width="2" fill="none"/><path d="M10 9h8M10 13h8M10 17h5" stroke="#192330" stroke-width="2"/></svg></div>
  <h3 style="margin-top:46px">Off the plan contracts</h3>
  <p>Experts in navigating the often complex world of off the plan development contracts.</p>
</div>
<div class="card" style="left:771px">
  <div class="badge"><svg width="30" height="30" viewBox="0 0 30 30"><rect x="6" y="5" width="18" height="20" rx="2" stroke="#fff" stroke-width="2" fill="none"/><path d="M10 11h10M10 15h10M10 19h6" stroke="#fff" stroke-width="2"/></svg></div>
  <h3 style="margin-top:42px">Put &amp; call option<br>agreements</h3>
  <p>Whether you're using a put and call option agreement for structuring or to help you on-sell for profit, we have you covered.</p>
</div>

<!-- services -->
<section class="abs services"></section>
<h2 class="section-title" style="top:1350px">Our services<span class="accent"></span></h2>
<div class="abs timeline"></div>
<div class="abs tl-dot"></div>
<div class="abs tl-icon" style="left:565px;top:1585px"><svg width="34" height="34" viewBox="0 0 34 34"><path d="M6 30V8h14v22M20 30V14h8v16M4 30h26M10 12h2M14 12h2M10 17h2M14 17h2M10 22h2M14 22h2" stroke="#0677BA" stroke-width="1.8" fill="none"/></svg></div>
<div class="abs tl-icon" style="left:565px;top:2003px"><svg width="34" height="34" viewBox="0 0 34 34"><circle cx="17" cy="11" r="6" stroke="#0677BA" stroke-width="1.8" fill="none"/><path d="M6 30c0-7 5-11 11-11s11 4 11 11z" stroke="#0677BA" stroke-width="1.8" fill="none"/></svg></div>

<div class="abs svc" style="left:150px;top:1452px;width:345px;text-align:right">
  <h3>Property development lawyers</h3>
  <p>Whether you're experienced in property development or are taking your first steps in this space there's one thing that doesn't change as you move in the property development area: a need for great property development lawyers to ensure your interests are protected.</p>
</div>
<div class="btn" style="left:346px;top:1734px;width:149px;height:38px">Find out more</div>
<svg class="abs" style="left:870px;top:1425px" width="195" height="300"><polygon points="0,0 195,0 195,300 175,300 175,20 0,20" fill="#0054AA"/></svg>
<div class="photo" role="img" aria-label="Modern two-storey white house with dark cladding lit at dusk" style="left:675px;top:1445px;width:370px;height:356px;background:linear-gradient(180deg,#7b8fa8 0%,#b7c3cf 45%,#4a4c50 80%,#3a3a36)"></div>

<svg class="abs" style="left:136px;top:2050px" width="240" height="192"><polygon points="0,0 20,0 20,172 240,172 240,192 0,192" fill="#0054AA"/></svg>
<div class="photo" role="img" aria-label="Lawyer pointing at a document while a colleague takes notes in a law library" style="left:156px;top:1865px;width:369px;height:357px;background:linear-gradient(135deg,#6b5a4c 0%,#8c7a68 40%,#2c2f36 75%,#d9d3cb)"></div>
<div class="abs svc" style="left:685px;top:1898px;width:400px">
  <h3>Conveyancing lawyers</h3>
  <p>Buying property and transferring title from one owner to another requires swift, accurate, and reliable conveyancing service. At Tallow Creek Lawyers our expert conveyancing lawyers make property transactions simple and hassle free. We ensure that nothing is forgotten</p>
</div>
<div class="btn" style="left:685px;top:2176px;width:149px;height:38px">Find out more</div>
<div class="btn" style="left:510px;top:2282px;width:182px;height:38px;background:var(--blue)">View more services</div>

<!-- free quote -->
<section class="abs quote-band"></section>
<h2 class="section-title" style="top:2442px;color:#fff">Get a free quote<span class="accent"></span></h2>
<div class="abs quote-card">
  <div class="abs" style="left:45px;top:45px;font-size:14.5px;color:var(--navy)">Enter Your Details Below and We'll Calculate Your Conveyancing fees in 30 seconds.</div>
  <div class="btn" style="left:725px;top:38px;width:62px;height:34px">Buy</div>
  <div class="btn" style="left:802px;top:38px;width:64px;height:34px;background:var(--navy)">Sell</div>

  <div class="q-label" style="left:48px;top:107px">What is the property type?</div>
  <div class="pill" style="left:288px;top:108px">House</div>
  <div class="pill" style="left:370px;top:108px">Townhouse</div>
  <div class="pill" style="left:476px;top:108px">Apartment/Unit</div>
  <div class="pill" style="left:614px;top:108px">Villa</div>
  <div class="pill" style="left:697px;top:108px">Land</div>
  <div class="pill" style="left:765px;top:108px">Off the plan</div>

  <div class="field" style="left:32px">First Name</div>
  <div class="field" style="left:250px">Last Name</div>
  <div class="field" style="left:468px">Email Address</div>
  <div class="field" style="left:685px">Phone Number</div>

  <div class="q-label" style="left:48px;top:270px;width:200px">When are you planning to buy/sell?</div>
  <div class="pill" style="left:294px;top:283px">Now</div>
  <div class="pill" style="left:372px;top:283px">Within a month</div>
  <div class="pill" style="left:508px;top:283px">1 to 3 months</div>
  <div class="pill" style="left:647px;top:283px">3 to 6 months</div>
  <div class="pill" style="left:775px;top:283px">6+ months</div>

  <div class="abs" style="left:47px;top:372px;width:20px;height:20px;border:1.5px solid #555"></div>
  <div class="abs" style="left:95px;top:360px;width:770px;font-size:13.5px;line-height:33px">I agree to receive marketing communications about my property journey from us (Northgate Media), our related companies and our trusted business partners.</div>
  <div class="btn" style="left:397px;top:454px;width:120px;height:38px">Submit now</div>
</div>

<!-- testimonials -->
<h2 class="abs" style="left:110px;top:3138px;font-size:28px;line-height:46px;color:var(--navy)">What our clients<br>say<span class="accent"></span></h2>
<div class="round-arrow" style="left:110px;top:3250px"><svg width="12" height="12" viewBox="0 0 12 12"><path d="M8 1L3 6l5 5" stroke="#192330" stroke-width="1.6" fill="none"/></svg></div>
<div class="round-arrow" style="left:164px;top:3250px"><svg width="12" height="12" viewBox="0 0 12 12"><path d="M4 1l5 5-5 5" stroke="#192330" stroke-width="1.6" fill="none"/></svg></div>

<div class="review" style="left:418px">
  <div class="rmark"></div>
  <div class="stars"><span></span><span></span><span></span><span></span><span></span></div>
  <p>Great advice and service on our property purchase. Kept us on track with reminders and key dates and actions. Professional and courteous, with a personable...</p>
  <div class="reviewer"><div class="avatar" style="background:#3d3d3d"></div><div><b>Mara Lindqvist</b><small>4 Months Ago</small></div></div>
</div>
<div class="review" style="left:718px">
  <div class="rmark"></div>
  <div class="stars"><span></span><span></span><span></span><span></span><span></span></div>
  <p>"Thanks Daniel stress free conveyancing service over the Xmas/ New year break.I would definitely recommend Daniel and his team. Third time with Daniel and his team...</p>
  <div class="reviewer"><div class="avatar" style="background:#2c3e5c"></div><div><b>Owen Castell</b><small>a month ago</small></div></div>
</div>
<div class="review" style="left:1016px;width:200px;padding-right:0">
  <div class="stars"><span></span><span></span><span></span></div>
  <p style="white-space:nowrap;overflow:hidden">"We could not be more t<br>Daniel and Renee for the<br>services they have given<br>ing our first home. Buyin<br>home was quite overwhe</p>
  <div class="reviewer"><div class="avatar" style="background:var(--blue-mid);color:#fff;display:flex;align-items:center;justify-content:center;font-size:24px">p</div><div><b>Priya N</b><small>6 years ago</small></div></div>
</div>

<!-- get started -->
<section class="abs started">
  <h2 class="section-title" style="top:66px;color:#fff">Would you like to get started with us?<span class="accent"></span></h2>
  <p class="abs" style="left:170px;top:118px;width:860px;text-align:center;color:#fff;font-size:14.5px;line-height:34px">Get in touch to see how we can help your with next property development project. We assist from site acquisition all the way through to conveyancing, and everything in between.</p>
  <div class="btn" style="left:535px;top:215px;width:130px;height:36px;font-family:'Jost',sans-serif;font-size:14px">07 3184 2290</div>
</section>

<!-- blog -->
<h2 class="section-title" style="top:3932px">From the blog<span class="accent"></span></h2>
<div class="round-arrow" style="left:38px;top:4114px"><svg width="12" height="12" viewBox="0 0 12 12"><path d="M8 1L3 6l5 5" stroke="#192330" stroke-width="1.6" fill="none"/></svg></div>
<div class="round-arrow" style="left:1130px;top:4114px"><svg width="12" height="12" viewBox="0 0 12 12"><path d="M4 1l5 5-5 5" stroke="#192330" stroke-width="1.6" fill="none"/></svg></div>
<article class="post" style="left:113px">
  <div class="img" role="img" aria-label="Construction cranes above a building site" style="background:linear-gradient(180deg,#d8d8d8,#9c9c9c 60%,#4a4a4a)"></div>
  <h4>Tips and traps when engaging a real estate agent for your next property development</h4>
  <p>One of the pivotal components of a successful property development is ensuring all lots...</p>
</article>
<article class="post" style="left:443px">
  <div class="img" role="img" aria-label="Apartment tower under construction" style="background:linear-gradient(180deg,#5e5e5e,#2f2f2f 60%,#8a8a8a)"></div>
  <h4>Developers: Ensure your development approval clause includes these items</h4>
  <p>One of the greatest risks for a developer buying an unapproved development site...</p>
</article>
<article class="post" style="left:773px">
  <div class="img" role="img" aria-label="Hands reviewing architectural plans on a desk" style="background:linear-gradient(135deg,#3b3b3b,#8a8680 55%,#c9c4bc)"></div>
  <h4>Developers: Ensure your due diligence clause includes these items</h4>
  <p>The most common condition for a developer to include in a contract when buying a development...</p>
</article>

<!-- offer -->
<section class="abs offer">
  <h2 class="abs" style="left:153px;top:38px;font-size:25px;color:#fff;letter-spacing:.5px">Special conditions or offer<span class="accent"></span></h2>
  <div class="btn" style="left:917px;top:37px;width:130px;height:38px;background:#fff;color:var(--navy)">Get offers</div>
</section>

<!-- footer -->
<footer class="abs footer">
  <div class="abs" style="left:120px;top:58px;font-size:26px;letter-spacing:8px;line-height:52px;font-weight:400">TALLOW<br>CREEK<br>LAWYERS</div>
  <p class="abs" style="left:122px;top:262px;font-size:12.5px;line-height:29px">© 2025 Tallow Creek Lawyers.<br>All Rights Reserved.</p>
  <h4 class="abs" style="left:459px;top:60px">Quick links</h4>
  <ul class="abs" style="left:459px;top:106px"><li>Home</li><li>Services</li><li>Resources</li><li>About Us</li><li>Contact Us</li></ul>
  <h4 class="abs" style="left:716px;top:60px">Contact us</h4>
  <div class="abs" style="left:716px;top:113px;display:flex;align-items:center;gap:34px;font-size:14.5px">
    <div class="icon-ring"><svg width="16" height="16" viewBox="0 0 24 24"><path fill="#7BADD7" d="M6.6 10.8c1.4 2.8 3.8 5.1 6.6 6.6l2.2-2.2c.3-.3.7-.4 1-.2 1.1.4 2.3.6 3.6.6.6 0 1 .4 1 1V20c0 .6-.4 1-1 1C10.6 21 3 13.4 3 4c0-.6.4-1 1-1h3.5c.6 0 1 .4 1 1 0 1.3.2 2.5.6 3.6.1.3 0 .7-.2 1l-2.3 2.2z"/></svg></div>
    (07) 3184 2290</div>
  <div class="abs" style="left:716px;top:182px;display:flex;align-items:center;gap:34px;font-size:14.5px">
    <div class="icon-ring"><svg width="16" height="16" viewBox="0 0 24 24"><rect x="2" y="5" width="20" height="14" rx="2" fill="#7BADD7"/><path d="M3 6l9 7 9-7" stroke="#192330" stroke-width="1.6" fill="none"/></svg></div>
    mail@tallowcreeklawyers.com.au</div>
  <div class="abs" style="left:716px;top:252px;display:flex;align-items:flex-start;gap:34px;font-size:14.5px;line-height:38px">
    <div class="icon-ring"><svg width="16" height="16" viewBox="0 0 24 24"><path fill="#7BADD7" d="M12 2a7 7 0 0 0-7 7c0 5 7 13 7 13s7-8 7-13a7 7 0 0 0-7-7zm0 9.5A2.5 2.5 0 1 1 12 6.5a2.5 2.5 0 0 1 0 5z"/></svg></div>
    <div style="margin-top:-2px">Kedron Park Centre, Level 2 Suite 14,<br>218 Gympie Road, Kedron,<br>Queensland 4031</div></div>
</footer>

</body>
</html>
```